UK landscaping company needs website

We, Brackwell Landscapes need a website design for a company based in Surrey, UK. The design should be bold and playful. We have three main areas of work driveways, paving and fencing. It shouldn't be too heavy in text and concentrate on the pictures from previous jobs we've completed. You may use stock images for the design, these can be changed if you are successful. Please don’t just copy the flyer it is just there to provide content.
We have a logo design which we would also like editing slightly.
Here are some of my local competitors
https://www.pelmarlandscapes.example.co.uk/

https://www.twinfirgardendesign.example.com/

https://kestbyrnlandscapes.example.co.uk/

Industry/Entity Type

Landscaping

Coding

Coded - Design and coding required

Number of Pages Required

3 page

Font styles to use
Sans Serif

Requirements
Must have
• Pictures of my previous jobs.
Must be mobile friendly
Easy to navigate
Nice to have
• Try to use different colours. It would be good to have some designs that aren’t just black and green.
I’d like some curves in the design.
Should not have
• We install hard landscaping. Think more building/construction and less plants and cutting grass.

```html
<!DOCTYPE html>
<html lang="en">
<head>
<meta charset="utf-8">
<title>Brackwell Landscapes – Home page concepts</title>
<link rel="stylesheet" href="https://fonts.googleapis.com/css2?family=Roboto:ital,wght@0,400;0,500;0,700;0,900;1,400&display=swap">
<style>
:root{
  --green:#5bb030;
  --green-dark:#4a9a24;
  --brown:#2e1a0c;
  --soft:#f0f0f0;
  --ink:#1b1b1b;
  --muted:#6b6b6b;
  --footer:#1e1e1e;
  --backdrop:#c9c9c9;
}
*{margin:0;padding:0;box-sizing:border-box}
html,body{width:1200px;height:2336px;overflow:hidden;background:var(--backdrop)}
body{font-family:"Roboto",Arial,sans-serif;color:var(--ink)}
.stage{position:absolute;left:0;top:0;width:1323px;height:2576px;transform:scale(0.9070);transform-origin:0 0}
.page{position:absolute;top:82px;width:572px;height:2411px;background:#fff;overflow:hidden}
.page--a{left:67px}
.page--b{left:685px}
.page *{position:absolute}
.page .inline,.page .inline *{position:static}

/* header */
.logo{left:53px;top:13px;font-size:19px;font-weight:900;letter-spacing:-.3px;color:var(--ink);display:flex;align-items:center;gap:4px}
.logo .dot{position:static;width:8px;height:8px;border-radius:50%;background:var(--green)}
.call{left:332px;top:9px;width:13px;height:19px;border:1.5px solid var(--green);border-radius:3px}
.call-label{left:350px;top:9px;font-size:5px;color:var(--muted)}
.call-number{left:350px;top:17px;font-size:10px;font-weight:700}
.btn{height:20px;border-radius:10px;font-size:6.5px;font-weight:700;color:#fff;background:var(--green);display:flex;align-items:center;justify-content:center;gap:3px;letter-spacing:.2px}
.btn--dark{background:var(--ink)}
.btn .arrow{position:static;width:6px;height:6px;border-radius:50%;background:#fff}
.quote-btn{left:433px;top:9px;width:86px}
.nav{top:40px;font-size:6px;font-weight:700;color:var(--ink)}
.nav--active{color:var(--green)}
.nav--active::after{content:"";position:absolute;left:0;right:0;bottom:-5px;height:1.5px;background:var(--green)}

/* hero */
.hero-photo{left:0;top:52px;width:572px;height:350px}
.page--a .hero-photo{background:linear-gradient(170deg,#3b2d23 0%,#4a3a2c 45%,#5b7d34 70%,#3f6a25 100%)}
.page--b .hero-photo{background:linear-gradient(180deg,#6e8c4c 0%,#7a5c3c 20%,#8d6a45 55%,#9a9486 75%,#62a43a 100%)}
.hero-title{left:53px;top:151px;font-size:20px;font-weight:700;color:#fff;letter-spacing:.2px}
.hero-copy{left:53px;top:183px;width:260px;font-size:7px;line-height:13px;color:#fff;font-weight:500}
.hero-btn{left:53px;top:226px;width:91px;background:var(--green);border:1.5px solid #fff}
.slide-arrow{top:189px;width:17px;height:17px;border:1px solid #fff;border-radius:50%}
.slide-arrow--prev{left:17px}
.slide-arrow--next{left:537px}
.slide-arrow::after{content:"";position:absolute;left:6px;top:5px;width:5px;height:5px;border-left:1px solid #fff;border-bottom:1px solid #fff;transform:rotate(45deg)}
.slide-arrow--next::after{left:4px;transform:rotate(-135deg)}

.bg{left:0;top:0;width:572px;height:2411px}

/* section titles */
.kicker{left:0;width:572px;text-align:center;font-size:7px;font-weight:700;color:var(--green)}
.title{left:0;width:572px;text-align:center;font-size:16px;font-weight:700;color:var(--ink)}
.title em{font-style:normal;color:var(--green)}
.title--light{color:#fff}
.rule{left:266px;width:40px;height:2px;background:var(--green)}
.body-copy{left:66px;width:440px;text-align:center;font-size:6.5px;line-height:13px;color:var(--muted)}

/* services */
.service-photo{width:126px;height:126px;border-radius:50%;border:3px solid #fff;box-shadow:0 1px 5px rgba(0,0,0,.25)}
.service-name{width:168px;text-align:center;font-size:7.5px;font-weight:700;top:773px}
.service-copy{width:168px;text-align:center;font-size:6px;line-height:10px;color:var(--muted);top:789px}
.service-link{width:168px;text-align:center;font-size:6px;font-weight:700;color:var(--green);top:817px}

/* why choose us */
.why-icon{width:28px;height:28px;border-radius:50%;background:#fff}
.why-icon svg{left:6px;top:6px;width:16px;height:16px}
.why-name{width:121px;text-align:center;font-size:7px;font-weight:700;color:#fff}
.why-copy{width:121px;text-align:center;font-size:6.5px;line-height:10.5px;color:#e8e1da}

/* gallery */
.tile{display:block}

/* testimonial */
.say-title{left:153px;top:1744px;font-size:15.5px;font-weight:700;color:#fff;letter-spacing:-.2px}
.avatar{left:82px;top:1772px;width:60px;height:60px;transform:rotate(45deg);border:2px solid #fff;background:linear-gradient(135deg,#7fb6d8,#3c76a8)}
.quote-mark{left:134px;top:1762px;font-size:24px;font-weight:900;color:rgba(255,255,255,.35);font-family:Georgia,serif}
.quote-mark--end{left:283px;top:1805px}
.quote-copy{left:153px;top:1777px;width:320px;font-size:6.5px;line-height:12.5px;font-style:italic;color:#fff}
.quote-name{left:153px;top:1822px;font-size:7px;font-weight:700;color:#fff}
.quote-org{left:153px;top:1834px;font-size:5px;color:#fff}
.say-arrow{top:1792px;width:9px;height:9px;border-left:1.5px solid #e6f2de;border-bottom:1.5px solid #e6f2de}
.say-arrow--prev{left:58px;transform:rotate(45deg)}
.say-arrow--next{left:505px;transform:rotate(-135deg)}

/* contact */
.contact-icon{width:40px;height:40px;border-radius:50%;background:var(--brown)}
.contact-icon svg{left:11px;top:11px;width:18px;height:18px}
.contact-label{font-size:7.5px;font-weight:700}
.contact-value{font-size:6.5px;line-height:11px;color:var(--muted)}
.field{left:59px;width:224px;height:25px;background:var(--soft);border:1px solid #e2e2e2;font-size:5.5px;color:var(--muted);padding:9px 0 0 18px}
.field--message{left:289px;top:2034px;height:87px}
.submit{left:254px;top:2142px;width:64px;height:18px}

/* footer */
.foot-logo{left:52px;top:2268px;font-size:24px;font-weight:900;color:#fff;letter-spacing:-.3px}
.social{top:2337px;width:12px;height:12px;border-radius:50%}
.foot-head{top:2263px;font-size:7px;font-weight:700;color:#fff}
.foot-list{top:2284px;font-size:5.5px;line-height:11px;color:#d8d8d8}
.foot-contact{left:425px;top:2283px;font-size:5.5px;line-height:8px;color:#d8d8d8}
.foot-contact b{color:#fff}
.to-top{left:540px;top:2341px;width:17px;height:17px;border-radius:50%;background:var(--green)}
.to-top::after{content:"";position:absolute;left:6px;top:7px;width:5px;height:5px;border-left:1.2px solid #fff;border-top:1.2px solid #fff;transform:rotate(45deg)}
.copyright{left:0;width:572px;top:2389px;text-align:center;font-size:6px;color:#d8d8d8}
</style>
</head>
<body>
<div class="stage">

<!-- ===================== Concept A ===================== -->
<section class="page page--a">
  <div class="hero-photo" role="img" aria-label="Photo of a finished garden with sleeper steps, artificial lawn, patio slabs and timber fencing"></div>
  <svg class="bg" viewBox="0 0 572 2411" aria-hidden="true">
    <path d="M0 383 Q286 318 572 383 L572 402 L0 402 Z" fill="#fff"/>
    <path d="M0 384 Q286 330 572 382 Q286 343 0 384 Z" fill="var(--green)"/>
    <rect x="0" y="568" width="572" height="300" fill="var(--soft)"/>
    <rect x="0" y="850" width="572" height="290" fill="var(--brown)"/>
    <path d="M0 848 Q286 902 572 848 Z" fill="var(--soft)"/>
    <path d="M22 858 Q286 900 550 855 Q286 888 22 858 Z" fill="var(--green)"/>
    <path d="M0 1136 Q286 1085 572 1136 L572 1142 L0 1142 Z" fill="#fff"/>
    <path d="M22 1132 Q286 1088 550 1130 Q286 1100 22 1132 Z" fill="var(--green)"/>
    <path d="M0 1715 Q300 1693 572 1668 L572 1882 Q300 1922 0 1922 Z" fill="var(--green)"/>
    <path d="M0 2196 Q286 2262 572 2196 L572 2411 L0 2411 Z" fill="var(--footer)"/>
    <path d="M10 2189 Q286 2248 560 2190 Q286 2232 10 2189 Z" fill="var(--green)"/>
  </svg>

  <div class="logo"><span>BRACKWELL</span><span class="dot"></span></div>
  <svg class="call" viewBox="0 0 13 19" aria-hidden="true"><path d="M4 6 Q3 10 7 13 L9 11.5 L10.5 13 L8.5 15 Q2 12 2.5 6 Z" fill="var(--green)"/></svg>
  <div class="call-label">CALL US</div>
  <div class="call-number">07700 900 418</div>
  <div class="btn quote-btn">REQUEST A QUOTE</div>
  <div class="nav nav--active" style="left:216px">HOME</div>
  <div class="nav" style="left:250px">ABOUT US</div>
  <div class="nav" style="left:297px">SERVICES</div>
  <div class="nav" style="left:342px">WORK GALLERY</div>
  <div class="nav" style="left:407px">CUSTOMER CARE</div>
  <div class="nav" style="left:477px">CONTACT US</div>

  <div class="slide-arrow slide-arrow--prev"></div>
  <div class="slide-arrow slide-arrow--next"></div>
  <h1 class="hero-title">BRACKWELL LANDSCAPES</h1>
  <p class="hero-copy">Lorem ipsum dolor sit amet, consectetur adipiscing elit, sed do eiusmod tempor incididunt ut labore et aliqua.</p>
  <div class="btn hero-btn">GET STARTED <span class="arrow"></span></div>

  <div class="kicker" style="top:399px">WELCOME TO</div>
  <h2 class="title" style="top:410px">BRACKWELL LANDSCAPES</h2>
  <div class="rule" style="top:433px"></div>
  <p class="body-copy" style="top:450px">Sed ut perspiciatis unde omnis iste natus error sit voluptatem accusantium doloremque laudantium, totam rem aperiam, eaque ipsa quae ab illo inventore veritatis et quasi architecto beatae vitae dicta sunt explicabo. Nemo enim ipsam voluptatem quia voluptas sit aspernatur aut odit aut fugit, sed quia consequuntur magni dolores eos qui ratione voluptatem sequi nesciunt.</p>
  <div class="btn btn--dark" style="left:202px;top:508px;width:77px">READ MORE <span class="arrow"></span></div>
  <div class="btn" style="left:292px;top:508px;width:77px">CONTACT US <span class="arrow"></span></div>

  <h2 class="title" style="top:598px">OUR <em>SERVICES</em></h2>
  <div class="rule" style="top:621px"></div>
  <div class="service-photo" style="left:55px;top:637px;background:linear-gradient(160deg,#4e7a35 0%,#6d6e72 35%,#8a8b8f 100%)" role="img" aria-label="Photo of a block paved driveway"></div>
  <div class="service-photo" style="left:223px;top:637px;background:linear-gradient(160deg,#6b3a24 0%,#8a5a3c 40%,#c9c9c6 70%,#5e8c3a 100%)" role="img" aria-label="Photo of a paved patio with timber pergola"></div>
  <div class="service-photo" style="left:391px;top:637px;background:linear-gradient(180deg,#6f8d55 0%,#8a6a45 40%,#6e5233 100%)" role="img" aria-label="Photo of new timber panel fencing"></div>
  <div class="service-name" style="left:34px">DRIVEWAYS</div>
  <div class="service-name" style="left:202px">PAVING</div>
  <div class="service-name" style="left:370px">FENCING</div>
  <p class="service-copy" style="left:34px">Lorem ipsum dolor sit amet, consectetur adipiscing elit, sed do eiusmod</p>
  <p class="service-copy" style="left:202px">Lorem ipsum dolor sit amet, consectetur adipiscing elit, sed do eiusmod</p>
  <p class="service-copy" style="left:370px">Lorem ipsum dolor sit amet, consectetur adipiscing elit, sed do eiusmod</p>
  <div class="service-link" style="left:30px">LEARN MORE ›</div>
  <div class="service-link" style="left:198px">LEARN MORE ›</div>
  <div class="service-link" style="left:366px">LEARN MORE ›</div>

  <h2 class="title title--light" style="top:917px;font-size:17px">WHY CHOOSE US</h2>
  <div class="rule" style="top:942px"></div>
  <div class="why-icon" style="left:90px;top:977px"><svg viewBox="0 0 16 16" aria-hidden="true"><rect x="3" y="1.5" width="10" height="13" rx="1" fill="none" stroke="var(--brown)" stroke-width="1.2"/><path d="M5 5h6M5 8h6M5 11h4" stroke="var(--brown)" stroke-width="1"/></svg></div>
  <div class="why-icon" style="left:211px;top:977px"><svg viewBox="0 0 16 16" aria-hidden="true"><circle cx="9" cy="6" r="4" fill="none" stroke="var(--brown)" stroke-width="1.2"/><path d="M7 6l1.5 1.5L11 5" fill="none" stroke="var(--brown)" stroke-width="1"/><path d="M1 13h4l3 1.5 6-3" fill="none" stroke="var(--brown)" stroke-width="1.2"/></svg></div>
  <div class="why-icon" style="left:332px;top:977px"><svg viewBox="0 0 16 16" aria-hidden="true"><circle cx="8" cy="4" r="2.2" fill="none" stroke="var(--brown)" stroke-width="1.2"/><circle cx="4" cy="9" r="1.8" fill="none" stroke="var(--brown)" stroke-width="1"/><circle cx="12" cy="9" r="1.8" fill="none" stroke="var(--brown)" stroke-width="1"/><path d="M1 15q3-4 6 0M9 15q3-4 6 0" fill="none" stroke="var(--brown)" stroke-width="1"/></svg></div>
  <div class="why-icon" style="left:453px;top:977px"><svg viewBox="0 0 16 16" aria-hidden="true"><rect x="2.5" y="1.5" width="9" height="13" rx="1" fill="none" stroke="var(--brown)" stroke-width="1.2"/><path d="M4.5 5h5M4.5 8h5" stroke="var(--brown)" stroke-width="1"/><circle cx="12" cy="11" r="2.5" fill="#fff" stroke="var(--brown)" stroke-width="1"/></svg></div>
  <div class="why-name" style="left:43px;top:1019px">Highly experienced</div>
  <div class="why-name" style="left:164px;top:1019px">Competitive rates</div>
  <div class="why-name" style="left:285px;top:1019px">Excellent workmanship</div>
  <div class="why-name" style="left:406px;top:1019px">Free quotations and advice</div>
  <p class="why-copy" style="left:43px;top:1035px">Lorem ipsum dolor sit amet, consectetur adipiscing elit, sed eiusmod tempor incididunt</p>
  <p class="why-copy" style="left:164px;top:1035px">Lorem ipsum dolor sit amet, consectetur adipiscing elit, sed eiusmod tempor incididunt</p>
  <p class="why-copy" style="left:285px;top:1035px">Lorem ipsum dolor sit amet, consectetur adipiscing elit, sed eiusmod tempor incididunt</p>
  <p class="why-copy" style="left:406px;top:1035px">Lorem ipsum dolor sit amet, consectetur adipiscing elit, sed eiusmod tempor incididunt</p>

  <h2 class="title" style="top:1153px;font-size:17px">WORK <em>GALLERY</em></h2>
  <div class="rule" style="top:1177px"></div>
  <div class="tile" style="left:54px;top:1197px;width:231px;height:133px;background:linear-gradient(160deg,#5f7a45 0%,#b8bcc2 25%,#3d4f6a 55%,#2e3c52 100%)" role="img" aria-label="Photo of a dark porcelain patio"></div>
  <div class="tile" style="left:287px;top:1197px;width:230px;height:133px;background:linear-gradient(150deg,#7a6a4a 0%,#5c9a33 30%,#8e8a80 60%,#6e5a46 100%)" role="img" aria-label="Photo of a patio with timber step edging"></div>
  <div class="tile" style="left:54px;top:1333px;width:154px;height:143px;background:linear-gradient(160deg,#b89a82,#a88872 60%,#8d7a6a)" role="img" aria-label="Photo of a circular paving feature"></div>
  <div class="tile" style="left:211px;top:1333px;width:150px;height:143px;background:linear-gradient(160deg,#c9a466 0%,#3f6a25 45%,#2f5a1e 80%,#8a6a40 100%)" role="img" aria-label="Photo of a raised lawn with sleeper edging"></div>
  <div class="tile" style="left:363px;top:1333px;width:154px;height:143px;background:linear-gradient(160deg,#4a3a32 0%,#c7c7c5 40%,#a9a9a7 75%,#8a5a3a 100%)" role="img" aria-label="Photo of grey stone steps"></div>
  <div class="tile" style="left:54px;top:1479px;width:231px;height:133px;background:linear-gradient(160deg,#a47a5c 0%,#2f9ad8 35%,#c49a7c 60%,#9c7a62 100%)" role="img" aria-label="Photo of a swimming pool surrounded by sandstone paving"></div>
  <div class="tile" style="left:287px;top:1479px;width:230px;height:133px;background:linear-gradient(160deg,#d9d9d9 0%,#8a6a45 35%,#4e3a2a 65%,#2a2a2a 100%)" role="img" aria-label="Photo of a timber pergola over a patio"></div>
  <div class="btn" style="left:234px;top:1638px;width:103px;height:22px">SEE ALL PROJECTS <span class="arrow"></span></div>

  <div class="say-arrow say-arrow--prev"></div>
  <div class="say-arrow say-arrow--next"></div>
  <h2 class="say-title">WHAT OUR CLIENTS HAVE TO SAY</h2>
  <div class="avatar" role="img" aria-label="Client portrait"></div>
  <div class="quote-mark">“</div>
  <div class="quote-mark quote-mark--end">”</div>
  <p class="quote-copy">Lorem ipsum dolor sit amet, consectetur adipiscing elit, sed do eiusmod tempor incididunt ut labore et dolore magna aliqua. Ut enim ad minim veniam, quis nostrud exercitation ullamco laboris nisi ut aliquip ex ea commodo consequat.</p>
  <div class="quote-name">Sam Ellery</div>
  <div class="quote-org">Company Name</div>

  <h2 class="title" style="top:1927px">CONTACT <em>US</em></h2>
  <div class="contact-icon" style="left:65px;top:1966px"><svg viewBox="0 0 18 18" aria-hidden="true"><path d="M9 16s-5-5.5-5-9a5 5 0 0110 0c0 3.5-5 9-5 9z" fill="none" stroke="#fff" stroke-width="1.4"/><circle cx="9" cy="7" r="1.8" fill="none" stroke="#fff" stroke-width="1.2"/></svg></div>
  <div class="contact-label" style="left:115px;top:1972px">Address</div>
  <p class="contact-value" style="left:115px;top:1984px;width:115px">Lorem ipsum dolor consectetur adipiscing elit,</p>
  <div class="contact-icon" style="left:240px;top:1966px"><svg viewBox="0 0 18 18" aria-hidden="true"><path d="M5 2l3 3-2 2q1.5 3 5 5l2-2 3 3-2 2Q7 15 3 4z" fill="none" stroke="#fff" stroke-width="1.3"/></svg></div>
  <div class="contact-label" style="left:289px;top:1978px">Phone</div>
  <p class="contact-value" style="left:289px;top:1990px">07700 900 418</p>
  <div class="contact-icon" style="left:361px;top:1966px"><svg viewBox="0 0 18 18" aria-hidden="true"><rect x="2" y="4" width="14" height="10" fill="none" stroke="#fff" stroke-width="1.3"/><path d="M2 4l7 6 7-6M2 14l5-5M16 14l-5-5" fill="none" stroke="#fff" stroke-width="1.1"/></svg></div>
  <div class="contact-label" style="left:412px;top:1978px">Emai</div>
  <p class="contact-value" style="left:412px;top:1990px;font-size:6px">info@brackwell-landscapes.example.com</p>
  <div class="field" style="top:2034px">First Name</div>
  <div class="field" style="top:2065px">Email Address</div>
  <div class="field" style="top:2096px">Phone Number</div>
  <div class="field field--message">Message</div>
  <div class="btn submit">SUBMIT</div>

  <div class="foot-logo">BRACKWELL</div>
  <div class="social" style="left:74px;background:#3b5bb0"></div>
  <div class="social" style="left:91px;background:#2a9ee8"></div>
  <div class="social" style="left:108px;background:#b0368a"></div>
  <div class="foot-head" style="left:195px">Quick Links</div>
  <p class="foot-list" style="left:195px">Home<br>About<br>Services<br>Projects<br>Our Team</p>
  <div class="foot-head" style="left:300px">About Company</div>
  <p class="foot-list" style="left:300px">Terms of Use<br>Terms &amp; Condition<br>News<br>Contact Us<br>FAQ</p>
  <div class="foot-head" style="left:414px">Contact Us</div>
  <p class="foot-contact"><b>Location</b><br>7 Lorem ipsum dolor sit amet,<br><b>Phone</b><br>07700 900 418<br><b>Fax</b><br>0123 456 7890<br><b>Email</b><br>info@brackwell-landscapes.example.com</p>
  <div class="to-top"></div>
  <div class="copyright">2020 Copyright - Brackwell Landscapes &nbsp;| All Rights Reserved</div>
</section>

<!-- ===================== Concept B ===================== -->
<section class="page page--b">
  <div class="hero-photo" role="img" aria-label="Photo of a new timber fence alongside a gravel border and lawn"></div>
  <svg class="bg" viewBox="0 0 572 2411" aria-hidden="true">
    <path d="M0 420 C120 340 230 380 330 378 C430 376 520 340 572 285 L572 402 L0 402 Z" fill="#fff"/>
    <path d="M0 420 C90 350 180 352 250 365 C330 380 420 372 572 288 L572 300 C440 392 330 396 240 378 C160 362 80 362 0 400 Z" fill="var(--green)"/>
    <path d="M0 402 L0 424 C40 400 60 390 100 378 C60 390 20 390 0 402 Z" fill="var(--green)"/>
    <rect x="0" y="568" width="572" height="300" fill="var(--soft)"/>
    <path d="M0 900 C50 860 120 855 250 858 C400 860 500 860 572 825 L572 1040 C520 1085 460 1115 330 1115 C200 1115 80 1110 0 1125 Z" fill="var(--brown)"/>
    <path d="M0 1712 C120 1700 180 1655 300 1670 C420 1685 500 1690 572 1658 L572 1870 C500 1915 420 1925 280 1905 C160 1890 80 1880 0 1905 Z" fill="var(--green)"/>
    <path d="M0 2215 C140 2190 240 2200 360 2215 C460 2225 530 2190 572 2140 L572 2411 L0 2411 Z" fill="var(--footer)"/>
    <path d="M200 2197 C330 2215 440 2222 520 2185 C545 2170 560 2155 572 2140 L572 2162 C520 2225 430 2238 360 2225 C300 2215 250 2205 200 2197 Z" fill="var(--green)"/>
  </svg>

  <div class="logo"><span>BRACKWELL</span><span class="dot"></span></div>
  <svg class="call" viewBox="0 0 13 19" aria-hidden="true"><path d="M4 6 Q3 10 7 13 L9 11.5 L10.5 13 L8.5 15 Q2 12 2.5 6 Z" fill="var(--green)"/></svg>
  <div class="call-label">CALL US</div>
  <div class="call-number">07700 900 418</div>
  <div class="btn quote-btn">REQUEST A QUOTE</div>
  <div class="nav nav--active" style="left:216px">HOME</div>
  <div class="nav" style="left:250px">ABOUT US</div>
  <div class="nav" style="left:297px">SERVICES</div>
  <div class="nav" style="left:342px">WORK GALLERY</div>
  <div class="nav" style="left:407px">CUSTOMER CARE</div>
  <div class="nav" style="left:477px">CONTACT US</div>

  <div class="slide-arrow slide-arrow--prev"></div>
  <div class="slide-arrow slide-arrow--next"></div>
  <h1 class="hero-title">BRACKWELL LANDSCAPES</h1>
  <p class="hero-copy">Lorem ipsum dolor sit amet, consectetur adipiscing elit, sed do eiusmod tempor incididunt ut labore et aliqua.</p>
  <div class="btn hero-btn">GET STARTED <span class="arrow"></span></div>

  <div class="kicker" style="top:399px">WELCOME TO</div>
  <h2 class="title" style="top:410px">BRACKWELL LANDSCAPES</h2>
  <div class="rule" style="top:433px"></div>
  <p class="body-copy" style="top:450px">Sed ut perspiciatis unde omnis iste natus error sit voluptatem accusantium doloremque laudantium, totam rem aperiam, eaque ipsa quae ab illo inventore veritatis et quasi architecto beatae vitae dicta sunt explicabo. Nemo enim ipsam voluptatem quia voluptas sit aspernatur aut odit aut fugit, sed quia consequuntur magni dolores eos qui ratione voluptatem sequi nesciunt.</p>
  <div class="btn btn--dark" style="left:202px;top:508px;width:77px">READ MORE <span class="arrow"></span></div>
  <div class="btn" style="left:292px;top:508px;width:77px">CONTACT US <span class="arrow"></span></div>

  <h2 class="title" style="top:598px">OUR <em>SERVICES</em></h2>
  <div class="rule" style="top:621px"></div>
  <div class="service-photo" style="left:55px;top:637px;background:linear-gradient(160deg,#4e7a35 0%,#6d6e72 35%,#8a8b8f 100%)" role="img" aria-label="Photo of a block paved driveway"></div>
  <div class="service-photo" style="left:223px;top:637px;background:linear-gradient(160deg,#6b3a24 0%,#8a5a3c 40%,#c9c9c6 70%,#5e8c3a 100%)" role="img" aria-label="Photo of a paved patio with timber pergola"></div>
  <div class="service-photo" style="left:391px;top:637px;background:linear-gradient(180deg,#6f8d55 0%,#8a6a45 40%,#6e5233 100%)" role="img" aria-label="Photo of new timber panel fencing"></div>
  <div class="service-name" style="left:34px">DRIVEWAYS</div>
  <div class="service-name" style="left:202px">PAVING</div>
  <div class="service-name" style="left:370px">FENCING</div>
  <p class="service-copy" style="left:34px">Lorem ipsum dolor sit amet, consectetur adipiscing elit, sed do eiusmod</p>
  <p class="service-copy" style="left:202px">Lorem ipsum dolor sit amet, consectetur adipiscing elit, sed do eiusmod</p>
  <p class="service-copy" style="left:370px">Lorem ipsum dolor sit amet, consectetur adipiscing elit, sed do eiusmod</p>
  <div class="service-link" style="left:30px">LEARN MORE ›</div>
  <div class="service-link" style="left:198px">LEARN MORE ›</div>
  <div class="service-link" style="left:366px">LEARN MORE ›</div>

  <h2 class="title title--light" style="top:917px;font-size:17px">WHY CHOOSE US</h2>
  <div class="rule" style="top:942px"></div>
  <div class="why-icon" style="left:90px;top:968px"><svg viewBox="0 0 16 16" aria-hidden="true"><rect x="3" y="1.5" width="10" height="13" rx="1" fill="none" stroke="var(--brown)" stroke-width="1.2"/><path d="M5 5h6M5 8h6M5 11h4" stroke="var(--brown)" stroke-width="1"/></svg></div>
  <div class="why-icon" style="left:211px;top:968px"><svg viewBox="0 0 16 16" aria-hidden="true"><circle cx="9" cy="6" r="4" fill="none" stroke="var(--brown)" stroke-width="1.2"/><path d="M7 6l1.5 1.5L11 5" fill="none" stroke="var(--brown)" stroke-width="1"/><path d="M1 13h4l3 1.5 6-3" fill="none" stroke="var(--brown)" stroke-width="1.2"/></svg></div>
  <div class="why-icon" style="left:332px;top:968px"><svg viewBox="0 0 16 16" aria-hidden="true"><circle cx="8" cy="4" r="2.2" fill="none" stroke="var(--brown)" stroke-width="1.2"/><circle cx="4" cy="9" r="1.8" fill="none" stroke="var(--brown)" stroke-width="1"/><circle cx="12" cy="9" r="1.8" fill="none" stroke="var(--brown)" stroke-width="1"/><path d="M1 15q3-4 6 0M9 15q3-4 6 0" fill="none" stroke="var(--brown)" stroke-width="1"/></svg></div>
  <div class="why-icon" style="left:453px;top:968px"><svg viewBox="0 0 16 16" aria-hidden="true"><rect x="2.5" y="1.5" width="9" height="13" rx="1" fill="none" stroke="var(--brown)" stroke-width="1.2"/><path d="M4.5 5h5M4.5 8h5" stroke="var(--brown)" stroke-width="1"/><circle cx="12" cy="11" r="2.5" fill="#fff" stroke="var(--brown)" stroke-width="1"/></svg></div>
  <div class="why-name" style="left:43px;top:1010px">Highly experienced</div>
  <div class="why-name" style="left:164px;top:1010px">Competitive rates</div>
  <div class="why-name" style="left:285px;top:1010px">Excellent workmanship</div>
  <div class="why-name" style="left:406px;top:1010px">Free quotations and advice</div>
  <p class="why-copy" style="left:43px;top:1026px">Lorem ipsum dolor sit amet, consectetur adipiscing elit, sed eiusmod tempor incididunt</p>
  <p class="why-copy" style="left:164px;top:1026px">Lorem ipsum dolor sit amet, consectetur adipiscing elit, sed eiusmod tempor incididunt</p>
  <p class="why-copy" style="left:285px;top:1026px">Lorem ipsum dolor sit amet, consectetur adipiscing elit, sed eiusmod tempor incididunt</p>
  <p class="why-copy" style="left:406px;top:1026px">Lorem ipsum dolor sit amet, consectetur adipiscing elit, sed eiusmod tempor incididunt</p>

  <h2 class="title" style="top:1153px;font-size:17px">WORK <em>GALLERY</em></h2>
  <div class="rule" style="top:1177px"></div>
  <div class="tile" style="left:54px;top:1197px;width:231px;height:133px;background:linear-gradient(160deg,#5f7a45 0%,#b8bcc2 25%,#3d4f6a 55%,#2e3c52 100%)" role="img" aria-label="Photo of a dark porcelain patio"></div>
  <div class="tile" style="left:287px;top:1197px;width:230px;height:133px;background:linear-gradient(150deg,#7a6a4a 0%,#5c9a33 30%,#8e8a80 60%,#6e5a46 100%)" role="img" aria-label="Photo of a patio with timber step edging"></div>
  <div class="tile" style="left:54px;top:1333px;width:154px;height:143px;background:linear-gradient(160deg,#b89a82,#a88872 60%,#8d7a6a)" role="img" aria-label="Photo of a circular paving feature"></div>
  <div class="tile" style="left:211px;top:1333px;width:150px;height:143px;background:linear-gradient(160deg,#c9a466 0%,#3f6a25 45%,#2f5a1e 80%,#8a6a40 100%)" role="img" aria-label="Photo of a raised lawn with sleeper edging"></div>
  <div class="tile" style="left:363px;top:1333px;width:154px;height:143px;background:linear-gradient(160deg,#4a3a32 0%,#c7c7c5 40%,#a9a9a7 75%,#8a5a3a 100%)" role="img" aria-label="Photo of grey stone steps"></div>
  <div class="tile" style="left:54px;top:1479px;width:231px;height:133px;background:linear-gradient(160deg,#a47a5c 0%,#2f9ad8 35%,#c49a7c 60%,#9c7a62 100%)" role="img" aria-label="Photo of a swimming pool surrounded by sandstone paving"></div>
  <div class="tile" style="left:287px;top:1479px;width:230px;height:133px;background:linear-gradient(160deg,#d9d9d9 0%,#8a6a45 35%,#4e3a2a 65%,#2a2a2a 100%)" role="img" aria-label="Photo of a timber pergola over a patio"></div>
  <div class="btn" style="left:234px;top:1638px;width:103px;height:22px">SEE ALL PROJECTS <span class="arrow"></span></div>

  <div class="say-arrow say-arrow--prev"></div>
  <div class="say-arrow say-arrow--next"></div>
  <h2 class="say-title">WHAT OUR CLIENTS HAVE TO SAY</h2>
  <div class="avatar" role="img" aria-label="Client portrait"></div>
  <div class="quote-mark">“</div>
  <div class="quote-mark quote-mark--end">”</div>
  <p class="quote-copy">Lorem ipsum dolor sit amet, consectetur adipiscing elit, sed do eiusmod tempor incididunt ut labore et dolore magna aliqua. Ut enim ad minim veniam, quis nostrud exercitation ullamco laboris nisi ut aliquip ex ea commodo consequat.</p>
  <div class="quote-name">Sam Ellery</div>
  <div class="quote-org">Company Name</div>

  <h2 class="title" style="top:1927px">CONTACT <em>US</em></h2>
  <div class="contact-icon" style="left:65px;top:1966px"><svg viewBox="0 0 18 18" aria-hidden="true"><path d="M9 16s-5-5.5-5-9a5 5 0 0110 0c0 3.5-5 9-5 9z" fill="none" stroke="#fff" stroke-width="1.4"/><circle cx="9" cy="7" r="1.8" fill="none" stroke="#fff" stroke-width="1.2"/></svg></div>
  <div class="contact-label" style="left:115px;top:1972px">Address</div>
  <p class="contact-value" style="left:115px;top:1984px;width:115px">Lorem ipsum dolor consectetur adipiscing elit,</p>
  <div class="contact-icon" style="left:240px;top:1966px"><svg viewBox="0 0 18 18" aria-hidden="true"><path d="M5 2l3 3-2 2q1.5 3 5 5l2-2 3 3-2 2Q7 15 3 4z" fill="none" stroke="#fff" stroke-width="1.3"/></svg></div>
  <div class="contact-label" style="left:289px;top:1978px">Phone</div>
  <p class="contact-value" style="left:289px;top:1990px">07700 900 418</p>
  <div class="contact-icon" style="left:361px;top:1966px"><svg viewBox="0 0 18 18" aria-hidden="true"><rect x="2" y="4" width="14" height="10" fill="none" stroke="#fff" stroke-width="1.3"/><path d="M2 4l7 6 7-6M2 14l5-5M16 14l-5-5" fill="none" stroke="#fff" stroke-width="1.1"/></svg></div>
  <div class="contact-label" style="left:412px;top:1978px">Emai</div>
  <p class="contact-value" style="left:412px;top:1990px;font-size:6px">info@brackwell-landscapes.example.com</p>
  <div class="field" style="top:2034px">First Name</div>
  <div class="field" style="top:2065px">Email Address</div>
  <div class="field" style="top:2096px">Phone Number</div>
  <div class="field field--message">Message</div>
  <div class="btn submit">SUBMIT</div>

  <div class="foot-logo">BRACKWELL</div>
  <div class="social" style="left:74px;background:#3b5bb0"></div>
  <div class="social" style="left:91px;background:#2a9ee8"></div>
  <div class="social" style="left:108px;background:#b0368a"></div>
  <div class="foot-head" style="left:195px">Quick Links</div>
  <p class="foot-list" style="left:195px">Home<br>About<br>Services<br>Projects<br>Our Team</p>
  <div class="foot-head" style="left:300px">About Company</div>
  <p class="foot-list" style="left:300px">Terms of Use<br>Terms &amp; Condition<br>News<br>Contact Us<br>FAQ</p>
  <div class="foot-head" style="left:414px">Contact Us</div>
  <p class="foot-contact"><b>Location</b><br>7 Lorem ipsum dolor sit amet,<br><b>Phone</b><br>07700 900 418<br><b>Fax</b><br>0123 456 7890<br><b>Email</b><br>info@brackwell-landscapes.example.com</p>
  <div class="to-top"></div>
  <div class="copyright">2020 Copyright - Brackwell Landscapes &nbsp;| All Rights Reserved</div>
</section>

</div>
</body>
</html>
```